New business card, letter head, email signature and Portfolio for our Security company.

We are an Crest security company that provides a top quality manpower services to protect high rise buildings, retail and all type of properties and would like a new business card/logo look.

- We would like the spot UV design.
- Matt black (double sided).
- We would like to incorporate a royal blue colour (feel free to experiment with it).
- Feel free to try different lengths with the card to make it stand out more than a normal business card.
- We would like the logo to be an eagle eye in the background (shines when card is tilted slightly in the background, either on the front, back or both sides of the card). Image attached as an example of eye shape (colour to be either black or royal blue).
- HARBOUR CREST SECURITY SERVICES PTY. LTD. and HCSS to be placed on one side of the card and on the other side of the card to have;

- Name in slightly bigger font than the position (directly on the bottom on the name).
- Mobile number
- Email address
- Website email address
- PO BOX address

Can we please have the files in a format that we can edit.

Reason: I need to consult my business partner with the designs so far and will make a decision from there.

Target Market(s)

Security Industry

Industry/Entity Type

Business

Contact Information for Business Card

- Mobile number
- Email address
- Website email address
- PO BOX address

Logo Text

HCSS and underneath the HCSS please add HARBOUR CREST SECURITY SERVICES PTY. LTD.

Font styles to use
Other font styles liked:
• bold type font

Colors
0255a3
000000

Requirements
Must have
• We are an Crest security company that provides a top quality manpower services to protect high rise buildings, retail and all type of properties and would like a new business card/logo look.
• - We would like the spot UV design.
• - Matt black (double sided).
• - We would like to incorporate a royal blue colour (feel free to experiment with it).
• - Feel free to try different lengths with the card to make it stand out more than a normal business card.
• - We would like the logo to be an eagle eye in the background (shines when card is tilted slightly in the background, either on the front, back or both sides of the card). Image attached as an example of eye shape (colour to be either black or royal blue).
• - HARBOUR CREST SECURITY SERVICES PTY. LTD. and HCSS to be placed on one side of the card and on the other side of the card to have;
• - Name in slightly bigger font than the position (directly on the bottom on the name).
• - Mobile number
• - Email address
• - Website email address
• - PO BOX address
• Can we please have the files in a format that we can edit.
Nice to have
• Feel free to try different lengths with the card to make it stand out more than a normal business card.
• Please find "URBAN JUNGLE" font attached and incorporate HCSS into the same style with building's inside the HCSS bold front also add HARBOUR into the bottom part of the S and follow on E - Crest on the bottom S - SECURITY on the bottom S - SERVICES on the bottom of each letter.
• other than that, I'll be happy with a bold modern font for the HCSS and HARBOUR CREST SECURITY SERVICES in a bold and thinner font underneath.

```html
<!DOCTYPE html>
<html lang="en">
<head>
<meta charset="UTF-8">
<title>Harbour Crest Security – Business Card</title>
<link href="https://fonts.googleapis.com/css2?family=Exo+2:wght@400;500;700;800&display=swap" rel="stylesheet">
<style>
  :root{
    --stage:#2b2b2b;
    --card:#262626;
    --card-edge:#1c1c1c;
    --silver:#b9b9b9;
    --silver-dim:#8d8d8d;
    --white:#f2f2f2;
    --royal:#3343b0;
    --rule:#6d6d6d;
  }
  *{margin:0;padding:0;box-sizing:border-box}
  html,body{width:1200px;height:1000px;overflow:hidden}
  body{
    background:var(--stage);
    font-family:"Exo 2",sans-serif;
    position:relative;
  }
  .card{
    position:absolute;
    left:220px;
    width:760px;
    height:420px;
    background:var(--card);
    border:1px solid var(--card-edge);
    box-shadow:0 14px 30px rgba(0,0,0,.45);
  }
  .card--front{top:50px}
  .card--back{top:520px}

  /* Front: company name */
  .brand{
    position:absolute;
    left:0;right:0;top:150px;
    display:flex;justify-content:center;align-items:flex-start;gap:18px;
  }
  .brand__dot{
    width:40px;height:40px;border-radius:50%;
    background:var(--silver);
    margin-top:4px;
  }
  .brand__text{display:flex;flex-direction:column;align-items:flex-end}
  .brand__name{
    font-weight:800;font-size:40px;letter-spacing:1px;
    color:var(--silver);line-height:1;
  }
  .brand__rule{
    width:100%;height:2px;background:var(--silver-dim);margin-top:8px;
  }
  .brand__sub{
    font-weight:700;font-size:14px;letter-spacing:2px;
    color:var(--silver);margin-top:6px;
  }

  /* Back: contact */
  .person{
    position:absolute;left:80px;top:100px;width:270px;text-align:right;
  }
  .person__name{
    font-weight:800;font-size:38px;color:var(--white);letter-spacing:1px;line-height:1.1;
  }
  .person__role{
    font-weight:400;font-size:28px;color:var(--royal);letter-spacing:1px;line-height:1.1;
  }
  .divider{
    position:absolute;left:372px;top:150px;width:2px;height:72px;background:var(--rule);
  }
  .contacts{
    position:absolute;left:395px;top:140px;list-style:none;
  }
  .contacts li{
    display:flex;align-items:center;height:32px;
    font-size:20px;color:var(--white);letter-spacing:.5px;
  }
  .contacts svg{width:16px;height:16px;margin-right:22px;fill:var(--royal)}
  .accent{color:var(--royal)}
  .address{
    position:absolute;left:180px;top:320px;
    display:flex;align-items:center;gap:12px;
    font-size:22px;color:var(--white);letter-spacing:.5px;
  }
  .address svg{width:18px;height:24px;fill:var(--royal)}
</style>
</head>
<body>

<section class="card card--front" aria-label="Card front">
  <div class="brand">
    <span class="brand__dot"></span>
    <div class="brand__text">
      <span class="brand__name">HARBOUR CREST SECURITY</span>
      <span class="brand__rule"></span>
      <span class="brand__sub">SERVICES PTY. LTD. and HCSS</span>
    </div>
  </div>
</section>

<section class="card card--back" aria-label="Card back">
  <div class="person">
    <div class="person__name">DANIEL REYES</div>
    <div class="person__role">OWNER</div>
  </div>
  <span class="divider"></span>
  <ul class="contacts">
    <li>
      <svg viewBox="0 0 24 24"><path d="M6.6 10.8a15 15 0 0 0 6.6 6.6l2.2-2.2c.3-.3.7-.4 1-.2 1.1.4 2.3.6 3.6.6.6 0 1 .4 1 1V20c0 .6-.4 1-1 1A17 17 0 0 1 3 4c0-.6.4-1 1-1h3.5c.6 0 1 .4 1 1 0 1.3.2 2.5.6 3.6.1.3 0 .7-.2 1z"/></svg>
      +000 123 456 789
    </li>
    <li>
      <svg viewBox="0 0 24 24"><path d="M2 5h20v14H2z M3.5 6.5 12 13l8.5-6.5z" fill-rule="evenodd"/></svg>
      yourname@email.com
    </li>
    <li>
      <svg viewBox="0 0 24 24"><path d="M10 2a8 8 0 0 1 6.3 12.9l5.4 5.4-1.4 1.4-5.4-5.4A8 8 0 1 1 10 2zm0 2.5a5.5 5.5 0 1 0 0 11 5.5 5.5 0 0 0 0-11z"/></svg>
      <span>www.<span class="accent">websitename</span>.com</span>
    </li>
  </ul>
  <div class="address">
    <svg viewBox="0 0 18 24"><path d="M9 0a9 9 0 0 1 9 9c0 6-9 15-9 15S0 15 0 9a9 9 0 0 1 9-9zm0 5.5a3.5 3.5 0 1 0 0 7 3.5 3.5 0 0 0 0-7z"/></svg>
    Your Street Address, Singapore, 1234
  </div>
</section>

</body>
</html>
```